New signage for apartment community in the Pacific Northwest

Signage for an apartment community in the Pacific Northwest. It should have a contemporary northwest vibe with a fresh exciting feeling. We are open to the colors cayenne, white, charcoal and a splash of lime green. Sign to have the name 'VOLTE' with the address number 28351 smaller underneath. sign can include a shape under the name or a feeling of energy in the shape of the name.

Target Market(s)

Young urban professionals

Industry/Entity Type

Real Estate Development

Requirements
Must have
• eyecatching
Should not have
• anything too cute or too busy

```html
<!DOCTYPE html>
<html lang="en">
<head>
<meta charset="utf-8">
<title>VOLTE Sign</title>
<link href="https://fonts.googleapis.com/css2?family=Open+Sans:wght@700;800&display=swap" rel="stylesheet">
<style>
  :root {
    --lime: #14f014;
    --charcoal: #37424a;
    --charcoal-light: #7d868c;
    --white: #ffffff;
    --backdrop: #eceeee;
  }
  html, body {
    margin: 0;
    padding: 0;
    width: 1200px;
    height: 2503px;
    overflow: hidden;
    background: var(--backdrop);
    font-family: "Open Sans", Arial, sans-serif;
  }
  .sign {
    position: absolute;
    left: 100px;
    top: 585px;
    width: 825px;
    height: 1100px;
    transform: scale(1.2121);
    transform-origin: 0 0;
    box-sizing: border-box;
    background: var(--white);
    border: 22px solid var(--lime);
    box-shadow: 0 20px 50px rgba(0,0,0,0.25);
  }
  .name-panel {
    position: absolute;
    left: 26px;
    top: 198px;
    width: 742px;
    height: 372px;
    background: var(--charcoal);
    border-radius: 22px;
    box-shadow: 0 30px 30px -22px rgba(0,0,0,0.45);
  }
  .name-panel::before {
    content: "";
    position: absolute;
    inset: 17px;
    border: 2px solid var(--lime);
    border-radius: 8px;
  }
  .name {
    position: absolute;
    left: 30px;
    right: 30px;
    top: 48px;
    margin: 0;
    text-align: center;
    color: var(--lime);
    font-weight: 800;
    font-size: 190px;
    line-height: 1;
    letter-spacing: -1px;
    white-space: nowrap;
  }
  .address {
    position: absolute;
    left: 147px;
    top: 268px;
    width: 457px;
    height: 63px;
    border-radius: 32px;
    background: var(--lime);
    color: var(--charcoal);
    font-weight: 700;
    font-size: 32px;
    display: flex;
    align-items: center;
    justify-content: center;
    gap: 10px;
    white-space: nowrap;
  }
  .address svg { width: 22px; height: 30px; }
  .call-label {
    position: absolute;
    left: 0;
    right: 0;
    top: 752px;
    margin: 0;
    text-align: center;
    color: var(--charcoal);
    font-weight: 800;
    font-size: 84px;
    line-height: 1;
  }
  .phone {
    position: absolute;
    left: 135px;
    top: 853px;
    width: 565px;
    height: 112px;
    box-sizing: border-box;
    border: 5px solid var(--lime);
    border-radius: 56px;
    background: linear-gradient(to bottom, var(--charcoal-light) 0%, #5f686e 45%, var(--charcoal) 55%, var(--charcoal) 100%);
    color: var(--lime);
    font-weight: 800;
    font-size: 66px;
    line-height: 102px;
    padding-left: 60px;
    text-align: center;
    letter-spacing: -1px;
    white-space: nowrap;
  }
  .phone-icon {
    position: absolute;
    left: 88px;
    top: 866px;
    width: 86px;
    height: 86px;
  }
</style>
</head>
<body>
  <div class="sign">
    <div class="name-panel">
      <h1 class="name">VOLTE</h1>
      <div class="address">
        <svg viewBox="0 0 22 30" aria-hidden="true">
          <path d="M11 1C5.5 1 1.5 5.2 1.5 10.5 1.5 17.5 11 29 11 29s9.5-11.5 9.5-18.5C20.5 5.2 16.5 1 11 1z" fill="none" stroke="#37424a" stroke-width="3"/>
          <circle cx="11" cy="10.5" r="3.6" fill="#37424a"/>
        </svg>
        <span>28351 Pacific Northwest</span>
      </div>
    </div>
    <p class="call-label">Call Now</p>
    <div class="phone">5206-314-770</div>
    <svg class="phone-icon" viewBox="0 0 86 86" aria-hidden="true">
      <circle cx="43" cy="43" r="40" fill="#14f014"/>
      <circle cx="43" cy="43" r="34" fill="#ffffff" stroke="#37424a" stroke-width="2"/>
      <path d="M30 27c2-2 4-2 5 0l4 6c1 2 0 3-1 4l-2 2c2 5 5 8 10 10l2-2c1-1 2-2 4-1l6 4c2 1 2 3 0 5l-3 3c-3 3-10 1-17-6s-10-14-7-17z" fill="#37424a"/>
      <path d="M46 27a13 13 0 0 1 12 12M47 20a20 20 0 0 1 18 18" fill="none" stroke="#37424a" stroke-width="3" stroke-linecap="round"/>
    </svg>
  </div>
</body>
</html>
```